Marlowe Group needs a business card

I would like the card to be simple but modern and elegant.
I like black and white.
or black and gold.
we are a private finance lender and also are involved in property and property developments.

please look at the business card photos i provided i would like M.G only one one side and all the other details on the other side use fonts that tie in with my theme.

Industry/Entity Type

Finance

Contact Information for Business Card

Marlowe Group (M.G) Daniel Marlowe M: 0413586207 E: danmarl@inboxmail.test

Font styles to use
Other font styles liked:
• Use fonts that would reflect our business

Colors
000000
ffffff

Requirements
Must have
• one side of details
• other side has either M.G or Marlowe Group like in the photos provided

```html
<!DOCTYPE html>
<html lang="en">
<head>
<meta charset="utf-8">
<title>Marlowe Group — Business Card</title>
<link rel="stylesheet" href="https://fonts.googleapis.com/css2?family=Open+Sans:wght@400;600;700&display=swap">
<style>
  :root {
    --backdrop: #ebebed;
    --card: #000000;
    --ink: #ffffff;
    --rule: rgba(255, 255, 255, 0.85);
    --card-w: 540px;
    --card-h: 309px;
  }
  * { box-sizing: border-box; margin: 0; padding: 0; }
  html, body {
    width: 1200px;
    height: 800px;
    overflow: hidden;
    background: var(--backdrop);
    font-family: "Open Sans", Arial, sans-serif;
  }
  .canvas {
    position: relative;
    width: 1200px;
    height: 800px;
  }
  .card {
    position: absolute;
    width: var(--card-w);
    height: var(--card-h);
    background: var(--card);
    color: var(--ink);
    box-shadow: 0 6px 18px rgba(0, 0, 0, 0.18);
  }
  .card--front { left: 70px; top: 100px; }
  .card--back  { left: 590px; top: 390px; }

  .monogram {
    position: absolute;
    left: 0; right: 0;
    top: 50%;
    transform: translateY(-50%);
    text-align: center;
    font-weight: 400;
    font-size: 62px;
    letter-spacing: 4px;
  }

  .wordmark {
    position: absolute;
    left: 70px;
    top: 176px;
    font-weight: 700;
    font-size: 34px;
    letter-spacing: -0.5px;
    line-height: 1;
  }

  .details {
    position: absolute;
    right: 36px;
    top: 72px;
    width: 210px;
    text-align: center;
  }
  .details__name {
    font-weight: 600;
    font-size: 18px;
    padding-bottom: 8px;
    border-bottom: 1px solid var(--rule);
  }
  .details__phone {
    font-size: 12px;
    padding: 8px 0 10px;
    border-bottom: 1px solid var(--rule);
  }
  .details__email {
    font-size: 12px;
    padding-top: 10px;
  }
</style>
</head>
<body>
  <main class="canvas">
    <section class="card card--front" aria-label="Card front">
      <div class="monogram">M.G</div>
    </section>

    <section class="card card--back" aria-label="Card back">
      <div class="wordmark">Marlowe Group</div>
      <div class="details">
        <p class="details__name">Daniel Marlowe</p>
        <p class="details__phone">0413586207</p>
        <p class="details__email">danmarl@inboxmail.test</p>
      </div>
    </section>
  </main>
</body>
</html>
```